Financial Advisor Resource Firm needs business card design

Need business card design for company in Omaha NE called Meridale Circle. We provide resources to financial advisors....workshop programs, retirement analysis, and insurance planning. I would like to see designs that use grays, greens, black, and white colors. The final design should communicate 'collaboration' and be simple yet attractive to financial planning clients. I will attached our logo and another picture of a puzzle piece coming together. I would like the incorporate the puzzle picture somehow, maybe on the back somehow, with color or just the gray scale....OR, the picture be the front of the card with 'Meridale' definition on it (see upload) and then company logo, employee name, title, address on the back (see ppt uploaded). The following disclosure needs to be included somewhere- Advisory services offered through Stonebrook Assets, LLC.
Updates

I uploaded a svg and ai file of the logo

Target Market(s)

Financial planning clients and financial advisors....so pretty diverse age range of about 40-70.

Industry/Entity Type

Financial Planning

Contact Information for Business Card

Tobias L. Fenwright, MBA
Founder/President
5287 E. Larkin Road
Suite 118
Ashgrove, KS 66210
Phone- (913) 555-0147
Cell- (913) 555-0183
Fax- (913) 555-0129
email- tobias@meridaleplan.example
web address- www.meridaleplan.example

Colors
1b1b1b
474747
d3d3d3
ffffff
9bcb3c
abd036

Requirements
Must have
• Must include logo provided, must be 2 sided, and must have disclosure...all of these items listed in project description

```html
<!DOCTYPE html>
<html lang="en">
<head>
<meta charset="utf-8">
<title>Meridale Circle – Business Card</title>
<link href="https://fonts.googleapis.com/css2?family=Lato:wght@400;700&display=swap" rel="stylesheet">
<style>
  :root{
    --ink:#1b1b1b;
    --charcoal:#474747;
    --mist:#d3d3d3;
    --paper:#ffffff;
    --leaf:#9bcb3c;
    --lime:#abd036;
    --stage:#3a3a3a;
  }
  *{margin:0;padding:0;box-sizing:border-box}
  html,body{width:1200px;height:896px;overflow:hidden}
  body{
    background:var(--stage);
    font-family:"Lato",sans-serif;
    display:flex;flex-direction:column;align-items:center;justify-content:center;gap:44px;
  }
  .card{width:640px;height:366px;position:relative;overflow:hidden;box-shadow:0 10px 24px rgba(0,0,0,.35)}

  /* front */
  .card--front{background:var(--paper);border-bottom:16px solid var(--leaf)}
  .holder{position:absolute;left:42px;top:52px}
  .holder__name{color:var(--leaf);font-weight:700;font-size:20px;letter-spacing:.5px;text-transform:uppercase}
  .holder__name .holder__degree{font-weight:400}
  .holder__title{color:var(--ink);font-size:16px;margin-top:2px}
  .contact{list-style:none;position:absolute;left:42px;top:126px;color:var(--ink);font-size:15px;line-height:22px}
  .contact li{display:flex;align-items:center;gap:10px}
  .contact svg{width:12px;height:12px;fill:var(--leaf);flex:none}
  .brand{position:absolute;right:44px;top:118px;text-align:right;color:var(--ink);
    font-weight:700;font-size:34px;letter-spacing:3px;text-transform:uppercase;line-height:1}
  .office{position:absolute;right:44px;bottom:30px;width:300px;text-align:right;color:var(--ink);font-size:15px;line-height:21px}
  .office__web{color:var(--charcoal);padding-bottom:8px;margin-bottom:8px;border-bottom:1px solid var(--mist)}
  .office__web span{color:var(--leaf)}

  /* back */
  .card--back{background:linear-gradient(135deg,var(--lime),var(--leaf) 60%,#8fbf33);color:var(--paper)}
  .brand--reverse{position:absolute;left:0;right:0;top:128px;text-align:center;color:var(--paper);
    font-weight:700;font-size:44px;letter-spacing:4px;text-transform:uppercase;line-height:1}
  .disclosure{position:absolute;left:50px;right:50px;top:236px;text-align:center;font-size:13px;
    letter-spacing:1px;text-transform:uppercase;padding-bottom:10px;border-bottom:1px solid rgba(255,255,255,.55)}
</style>
</head>
<body>
  <section class="card card--front" aria-label="Business card front">
    <div class="holder">
      <p class="holder__name">Tobias L. Fenwright, <span class="holder__degree">MBA</span></p>
      <p class="holder__title">Founder/President</p>
    </div>
    <ul class="contact">
      <li><svg viewBox="0 0 16 16" aria-hidden="true"><path d="M3 1h3l1.5 4-2 1.3a9 9 0 0 0 4.2 4.2L11 8.5l4 1.5v3a2 2 0 0 1-2 2A12 12 0 0 1 1 3a2 2 0 0 1 2-2z"/></svg>(913) 555-0147</li>
      <li><svg viewBox="0 0 16 16" aria-hidden="true"><path d="M4 0h8a1 1 0 0 1 1 1v14a1 1 0 0 1-1 1H4a1 1 0 0 1-1-1V1a1 1 0 0 1 1-1zm1 2v10h6V2z"/></svg>(913) 555-0183</li>
      <li><svg viewBox="0 0 16 16" aria-hidden="true"><path d="M4 0h7v5H4zM1 6h14v7h-3v3H4v-3H1zm5 6v2h4v-2z"/></svg>(913) 555-0129</li>
      <li><svg viewBox="0 0 16 16" aria-hidden="true"><path d="M0 3h16v10H0zm1.5 1.2L8 9l6.5-4.8V4h-13z"/></svg>tobias@meridaleplan.example</li>
    </ul>
    <p class="brand">Meridale Circle</p>
    <div class="office">
      <p class="office__web">www.meridaleplan.<span>example</span></p>
      <p>5287 E. Larkin Road</p>
      <p>Suite 118 Ashgrove, KS 66210</p>
    </div>
  </section>

  <section class="card card--back" aria-label="Business card back">
    <p class="brand--reverse">Meridale Circle</p>
    <p class="disclosure">Advisory services offered through Stonebrook Assets, LLC.</p>
  </section>
</body>
</html>
```